Zvo Klinieken website for a maxillofacial surgery clinic

It's a website for a clinic for maxillofacial surgery in WordPress . The website doesn't need to be complicated but has to look professional. It needs to be in Dutch so i can give the texts. Similar websites are www.tandartsenpraktijkveldorm.nl or www.pbtspecialisten.nl. Pages would be sort of similar to https://hetcentrumvoorgezichtszorg.nl/ or https://wervelmondclinics.nl/. Those lasts are maxillofacial surgery clinic websites, but there are little more extensive.
I uploaded the logo. If this is not the proper quality i can upload the eps. Logo was made through pixelforum.

Target Market(s)

Patients who can find me and see information about the clinic

Industry/Entity Type

Healthcare

Coding

Coded - Design and coding required

Number of Pages Required

5+ page

Font styles to use
Other font styles liked:
• Something standard professional

Colors
0054AA
0677BA
7BADD7
CADEEF
E8F1F8

Requirements
Nice to have
• Something in line with the logo. I prefer a little dark like the darker logos but I'm not sure if that's professional. Logos bkvzo and rlpw are instances i'm registered to so they will have to be on the website too but small somewhere.

```html
<!DOCTYPE html>
<html lang="nl">
<head>
<meta charset="utf-8">
<title>Zvo Klinieken</title>
<link href="https://fonts.googleapis.com/css2?family=Montserrat:wght@500;600;700&family=Lato:wght@400;700&family=Roboto:wght@400;500&display=swap" rel="stylesheet">
<style>
:root{
  --blue:#2ea3dc;
  --slate:#62809f;
  --light:#eef6fd;
  --ink:#2b2b2b;
  --dark:#161616;
  --grad:linear-gradient(90deg,#2aa6e0,#6a84a8);
}
*{margin:0;padding:0;box-sizing:border-box}
html,body{width:1200px;height:3572px;overflow:hidden}
body{font-family:'Lato',sans-serif;color:var(--ink);background:#fff;position:relative}
.abs{position:absolute}
section,header,footer,.topbar{position:absolute;left:0;width:1200px}
.btn{position:absolute;display:flex;align-items:center;justify-content:center;background:var(--grad);color:#fff;font-family:'Montserrat',sans-serif;font-weight:700;font-size:15px;border-radius:30px;box-shadow:0 4px 8px rgba(0,0,0,.2);letter-spacing:.2px}
.heading{position:absolute;font-family:'Montserrat',sans-serif;font-weight:700;color:var(--blue);font-size:36px;letter-spacing:.5px}

.topbar{top:0;height:55px;background:var(--blue);color:#fff;font-family:'Roboto',sans-serif;font-size:15px}
.topbar span{position:absolute;top:17px}
.topbar .sep{width:1px;height:14px;background:rgba(255,255,255,.7);top:21px}

header{top:55px;height:102px;background:#fff}
.logo-box{position:absolute;left:111px;top:-16px;width:208px;height:133px;background:#fff;border-radius:22px;display:flex;align-items:center;justify-content:center;box-shadow:0 2px 6px rgba(0,0,0,.08);z-index:2}
.logo-box .name{font-family:'Montserrat',sans-serif;font-weight:700;color:var(--blue);font-size:26px;text-align:center;line-height:1.1}
.nav{position:absolute;top:41px;font-family:'Roboto',sans-serif;font-size:14px;color:#333}
.nav.active{color:var(--blue);font-weight:500;text-decoration:underline;text-underline-offset:4px}
.contact-btn{left:949px;top:30px;width:140px;height:44px;font-size:14px}

.hero{top:157px;height:540px;background:linear-gradient(100deg,#4a4442 0%,#6b615c 45%,#a89489 75%,#cdb6a8 100%)}
.hero .welcome{left:111px;top:150px;color:#fff;font-family:'Montserrat',sans-serif;font-weight:700;font-size:26px}
.hero h1{position:absolute;left:108px;top:185px;color:#fff;font-family:'Montserrat',sans-serif;font-weight:600;font-size:58px;letter-spacing:1px}
.hero p{left:111px;top:276px;color:#fff;font-size:16px;line-height:28px}
.hero .btn{left:111px;top:352px;width:251px;height:50px}

.services{top:697px;height:790px;background:#fff}
.services .heading{left:0;width:1200px;text-align:center;top:70px}
.services .sub{left:0;width:1200px;text-align:center;top:155px;font-family:'Roboto',sans-serif;font-size:17px;color:#666}
.card{position:absolute;top:211px;width:308px;height:486px;background:#fff;box-shadow:0 2px 10px rgba(0,0,0,.12);text-align:center}
.card h3{margin-top:22px;font-family:'Montserrat',sans-serif;font-weight:500;font-size:19px;color:#222}
.card .photo{width:215px;height:215px;border-radius:50%;margin:20px auto 0;border:3px solid #5e7ea6}
.card p{font-size:14px;line-height:27.5px;color:#444;padding:0 16px;margin-top:18px}
.card .more{position:absolute;left:80px;bottom:26px;width:147px;height:45px;border:2.5px solid #5e7ea6;border-radius:24px;display:flex;align-items:center;justify-content:center;font-family:'Montserrat',sans-serif;font-weight:600;font-size:14px;color:#5e7ea6;background:#fff}
.card.featured{background:linear-gradient(180deg,#2fa5df,#6683a6)}
.card.featured h3{color:#fff;font-weight:700;font-size:22px}
.card.featured .photo{border:5px solid #fff}
.card.featured p{color:#fff}
.card.featured .more{border:none}
.arrow{position:absolute;top:432px}

.about{top:1487px;height:534px;background:var(--light)}
.about .brand{left:108px;top:150px;width:416px;font-family:'Montserrat',sans-serif;font-weight:700;color:var(--blue);font-size:64px;line-height:1.05}
.about .heading{left:608px;top:78px}
.about .copy{left:576px;top:150px;width:510px;font-size:14.5px;line-height:30px;color:#222}
.about .copy p+p{margin-top:30px}
.about .btn{left:576px;top:414px;width:173px;height:51px}

.budget{top:2021px;height:549px;background:linear-gradient(90deg,#8a7a6c 0%,#b4a595 40%,#6e5a4c 70%,#5a6a82 100%)}
.budget .box{position:absolute;left:108px;top:90px;width:531px;height:370px;background:#fff;text-align:center}
.budget h2{font-family:'Montserrat',sans-serif;font-weight:700;color:var(--blue);font-size:36px;margin-top:30px}
.budget .box p{font-family:'Roboto',sans-serif;font-size:15px;color:#555;line-height:33px;padding:0 40px}
.budget .btn{left:143px;top:275px;width:245px;height:51px}

.reviews{top:2570px;height:590px;background:#fff}
.reviews .heading{left:0;width:1200px;text-align:center;top:65px}
.avatar{position:absolute;border-radius:50%;background:linear-gradient(160deg,#c9b3a2,#7a5e4c)}
.dot{position:absolute;border-radius:50%}
.quote{position:absolute;font-family:Georgia,serif;font-size:190px;color:#e2e2e2;line-height:1}
.reviews .name{left:0;width:1200px;text-align:center;top:276px;font-family:'Montserrat',sans-serif;font-weight:600;font-size:19px}
.reviews .country{left:0;width:1200px;text-align:center;top:312px;font-family:'Montserrat',sans-serif;font-size:12px;color:#555}
.reviews .stars{left:0;width:1200px;text-align:center;top:330px;font-size:30px;color:#f2b01e;letter-spacing:1px}
.reviews .text{left:258px;width:684px;text-align:center;top:376px;font-size:15px;line-height:30px;color:#444}

footer{top:3160px;height:412px;background:var(--dark);color:#fff}
footer .brand{left:111px;top:90px;font-family:'Montserrat',sans-serif;font-weight:700;color:var(--blue);font-size:32px;line-height:1.1}
footer .social{position:absolute;top:221px;width:28px;height:28px;border-radius:50%;background:#fff}
footer h4{position:absolute;top:70px;font-family:'Montserrat',sans-serif;font-weight:500;font-size:16px;letter-spacing:.3px}
footer ul{position:absolute;top:112px;list-style:none;font-size:15px}
footer li{height:34.5px;display:flex;align-items:center;gap:10px}
footer li svg{flex:none}
.contact-row{position:absolute;left:884px;display:flex;gap:14px;align-items:flex-start;font-size:15px;line-height:28px}
.contact-row .ic{width:30px;height:30px;border-radius:50%;background:#fff;display:flex;align-items:center;justify-content:center;flex:none}
footer .rule{position:absolute;left:108px;top:314px;width:976px;height:1px;background:#555}
footer .copy{position:absolute;left:0;width:1200px;text-align:center;top:352px;font-size:15px}
</style>
</head>
<body>

<div class="topbar">
  <span style="left:546px">In</span>
  <span style="left:566px;top:16px"><svg width="28" height="20" viewBox="0 0 28 20"><circle cx="10" cy="10" r="8.5" fill="none" stroke="#fff" stroke-width="1.5"/><ellipse cx="10" cy="10" rx="3.5" ry="8.5" fill="none" stroke="#fff" stroke-width="1.3"/><line x1="1.5" y1="10" x2="18.5" y2="10" stroke="#fff" stroke-width="1.3"/><path d="M22 11l3 3 3-3z" fill="#fff"/></svg></span>
  <div class="sep abs" style="left:630px"></div>
  <span style="left:652px;top:18px"><svg width="14" height="14" viewBox="0 0 24 24"><path fill="#fff" d="M6.6 10.8a15 15 0 006.6 6.6l2.2-2.2c.3-.3.7-.4 1-.2 1.1.4 2.3.6 3.6.6.6 0 1 .4 1 1V20c0 .6-.4 1-1 1A17 17 0 013 4c0-.6.4-1 1-1h3.5c.6 0 1 .4 1 1 0 1.3.2 2.5.6 3.6.1.3 0 .7-.2 1z"/></svg></span>
  <span style="left:676px">+1 555 010 2040</span>
  <div class="sep abs" style="left:817px"></div>
  <span style="left:843px;top:18px"><svg width="12" height="15" viewBox="0 0 24 30"><path fill="#fff" d="M12 0a11 11 0 00-11 11c0 8 11 19 11 19s11-11 11-19A11 11 0 0012 0zm0 15a4 4 0 110-8 4 4 0 010 8z"/></svg></span>
  <span style="left:868px">Zvo Klinieken, Verenigde Staten</span>
</div>

<header>
  <div class="logo-box"><div class="name">Zvo<br>Klinieken</div></div>
  <span class="nav active" style="left:437px">THUIS</span>
  <span class="nav" style="left:513px">OVER ONS</span>
  <span class="nav" style="left:624px">DIENSTEN</span>
  <span class="nav" style="left:732px">SPECIALE AANBIEDINGEN</span>
  <div class="btn contact-btn">NEEM CONTACT</div>
</header>

<section class="hero" role="img" aria-label="Foto van een lachende patiënte bij een tandheelkundig onderzoek">
  <div class="abs welcome">WELKOM BIJ</div>
  <h1>ZVO KLINIEKEN</h1>
  <p class="abs">Itaque earum rerum hic tenetur a sapiente delectus,<br>ut aut reiciendis voluptatibus maiores</p>
  <div class="btn">EEN AFSPRAAK MAKEN</div>
</section>

<section class="services">
  <h2 class="heading">ONZE DIENSTEN</h2>
  <div class="abs sub">Temporibus autem quibusdam et aut officiis debitis aut rerum necessitatibus</div>
  <svg class="arrow" style="left:42px" width="28" height="14" viewBox="0 0 28 14"><path d="M27 7H2M8 1L2 7l6 6" fill="none" stroke="#2ea3dc" stroke-width="2"/></svg>
  <svg class="arrow" style="left:1134px" width="28" height="14" viewBox="0 0 28 14"><path d="M1 7h25M20 1l6 6-6 6" fill="none" stroke="#2ea3dc" stroke-width="2"/></svg>

  <div class="card" style="left:111px">
    <h3>KAAKCHIRURGIE</h3>
    <div class="photo" role="img" aria-label="Foto van een tandarts met een lachende patiënt in de stoel" style="background:linear-gradient(150deg,#dfe6ea,#9fb1bd)"></div>
    <p>Temporibus autem quibusdam et aut officiis debitis aut rerum necessitatibus saepe eveniet ut et voluptates repudiandae sint et molestiae non recusandae</p>
    <div class="more">LEES VERDER</div>
  </div>
  <div class="card featured" style="left:447px">
    <h3>VERWIJSPRAKTIJK</h3>
    <div class="photo" role="img" aria-label="Foto van een lachend kind bij een controle" style="background:linear-gradient(150deg,#c8d7e3,#6d8fa9)"></div>
    <p>Itaque earum rerum hic tenetur a sapiente delectus, ut aut reiciendis voluptatibus maiores alias consequatur aut perferendis doloribus asperiores repellat.</p>
    <div class="more">LEES VERDER</div>
  </div>
  <div class="card" style="left:781px">
    <h3>VERWIJZER</h3>
    <div class="photo" role="img" aria-label="Foto van een tandarts die een patiënte behandelt" style="background:linear-gradient(150deg,#eef1f3,#a9b5bf)"></div>
    <p>Autem quibusdam et aut officiis debitis aut rerum necessitatibus saepe eveniet ut et voluptates repudiandae sint et molestiae non recusandae</p>
    <div class="more">LEES VERDER</div>
  </div>
</section>

<section class="about">
  <div class="abs brand">Zvo<br>Klinieken</div>
  <h2 class="heading">OVER ONS ZVO KLINIEKEN</h2>
  <div class="abs copy">
    <p>Nam libero tempore, cum soluta nobis est eligendi optio cumque nihil impedit voluptas assumenda est, omnis dolor repellendus. Temporibus autem quibusdam et aut officiis debitis aut rerum necessitatibus saepe eveniet ut et voluptates repudiandae sint et molestiae non recusandae.</p>
    <p>Itaque earum rerum hic tenetur a sapiente delectus, ut aut reiciendis voluptatibus maiores alias consequatur aut perferendis doloribus asperiores repellat.</p>
  </div>
  <div class="btn">BEKIJK MEER</div>
</section>

<section class="budget" role="img" aria-label="Foto van een lachende vrouw in een wazige omgeving">
  <div class="box">
    <h2>BESPAAR UW BUDGET</h2>
    <p style="margin-top:16px">Temporibus autem quibusdam et aut officiis debitis aut rerum udiandae sint et molestiae non recusandae.</p>
    <p style="margin-top:33px">Itaque earum rerum hic tenetur a sapiente delectus, ut aut tur aut perferendis doloribus asperiores repellat.</p>
    <div class="btn">MAAK EEN AFSPRAAK</div>
  </div>
</section>

<section class="reviews">
  <h2 class="heading">WAT KLANT ZEGT</h2>
  <div class="avatar" role="img" aria-label="Portretfoto van een klant" style="left:546px;top:145px;width:106px;height:106px"></div>
  <div class="avatar" role="img" aria-label="Portretfoto van een klant" style="left:118px;top:196px;width:66px;height:66px"></div>
  <div class="avatar" role="img" aria-label="Portretfoto van een klant" style="left:995px;top:121px;width:46px;height:46px;background:linear-gradient(160deg,#ddd,#999)"></div>
  <div class="dot" style="left:362px;top:233px;width:14px;height:14px;background:#8cc63f"></div>
  <div class="dot" style="left:876px;top:197px;width:7px;height:7px;background:var(--blue)"></div>
  <div class="quote" style="left:140px;top:270px">“</div>
  <div class="quote" style="left:963px;top:375px">”</div>
  <div class="abs name">DAAN VERHOEF</div>
  <div class="abs country">Verenigde Staten</div>
  <div class="abs stars">★★★★★</div>
  <div class="abs text">Temporibus autem qpe eveniet ut et voluptates repudiandae sint et molestiae non recusandae. Itaque earum rerum hic tenetur a sapiente delectus, ut aut reiciendis voluptatibus maiores alias consequatur aut perferendis doloribus asperiores repellat.</div>
  <div class="dot" style="left:573px;top:501px;width:13px;height:13px;background:#d6dcf0"></div>
  <div class="dot" style="left:593px;top:500px;width:15px;height:15px;background:var(--blue)"></div>
  <div class="dot" style="left:615px;top:501px;width:13px;height:13px;background:#d6dcf0"></div>
</section>

<footer>
  <div class="abs brand">Zvo<br>Klinieken</div>
  <div class="social" style="left:121px"></div>
  <div class="social" style="left:171px"></div>
  <div class="social" style="left:222px"></div>
  <div class="social" style="left:273px"></div>

  <h4 style="left:391px">SNELLE KOPPELINGEN</h4>
  <ul style="left:391px">
    <li><svg width="14" height="14" viewBox="0 0 14 14"><circle cx="7" cy="7" r="7" fill="#fff"/><path d="M4 7h6M7 4l3 3-3 3" stroke="#161616" stroke-width="1.6" fill="none"/></svg>Thuis</li>
    <li><svg width="14" height="14" viewBox="0 0 14 14"><circle cx="7" cy="7" r="7" fill="#fff"/><path d="M4 7h6M7 4l3 3-3 3" stroke="#161616" stroke-width="1.6" fill="none"/></svg>Over</li>
    <li><svg width="14" height="14" viewBox="0 0 14 14"><circle cx="7" cy="7" r="7" fill="#fff"/><path d="M4 7h6M7 4l3 3-3 3" stroke="#161616" stroke-width="1.6" fill="none"/></svg>Diensten</li>
    <li><svg width="14" height="14" viewBox="0 0 14 14"><circle cx="7" cy="7" r="7" fill="#fff"/><path d="M4 7h6M7 4l3 3-3 3" stroke="#161616" stroke-width="1.6" fill="none"/></svg>Getuigenissen</li>
    <li><svg width="14" height="14" viewBox="0 0 14 14"><circle cx="7" cy="7" r="7" fill="#fff"/><path d="M4 7h6M7 4l3 3-3 3" stroke="#161616" stroke-width="1.6" fill="none"/></svg>Neem contact</li>
  </ul>

  <h4 style="left:627px">HULPKOPPELINGEN</h4>
  <ul style="left:627px">
    <li><svg width="14" height="14" viewBox="0 0 14 14"><circle cx="7" cy="7" r="7" fill="#fff"/><path d="M4 7h6M7 4l3 3-3 3" stroke="#161616" stroke-width="1.6" fill="none"/></svg>FAQ</li>
    <li><svg width="14" height="14" viewBox="0 0 14 14"><circle cx="7" cy="7" r="7" fill="#fff"/><path d="M4 7h6M7 4l3 3-3 3" stroke="#161616" stroke-width="1.6" fill="none"/></svg>Gebruiksvoorwaarden</li>
    <li><svg width="14" height="14" viewBox="0 0 14 14"><circle cx="7" cy="7" r="7" fill="#fff"/><path d="M4 7h6M7 4l3 3-3 3" stroke="#161616" stroke-width="1.6" fill="none"/></svg>Privacybeleid</li>
    <li><svg width="14" height="14" viewBox="0 0 14 14"><circle cx="7" cy="7" r="7" fill="#fff"/><path d="M4 7h6M7 4l3 3-3 3" stroke="#161616" stroke-width="1.6" fill="none"/></svg>Ondersteuningskoppelingen</li>
    <li><svg width="14" height="14" viewBox="0 0 14 14"><circle cx="7" cy="7" r="7" fill="#fff"/><path d="M4 7h6M7 4l3 3-3 3" stroke="#161616" stroke-width="1.6" fill="none"/></svg>Voorwaarden</li>
  </ul>

  <h4 style="left:884px">NEEM CONTACT</h4>
  <div class="contact-row" style="top:112px">
    <div class="ic"><svg width="12" height="15" viewBox="0 0 24 30"><path fill="#161616" d="M12 0a11 11 0 00-11 11c0 8 11 19 11 19s11-11 11-19A11 11 0 0012 0zm0 15a4 4 0 110-8 4 4 0 010 8z"/></svg></div>
    <div>Zvo Klinieken<br>Verenigde Staten</div>
  </div>
  <div class="contact-row" style="top:194px">
    <div class="ic"><svg width="14" height="14" viewBox="0 0 24 24"><path fill="#161616" d="M6.6 10.8a15 15 0 006.6 6.6l2.2-2.2c.3-.3.7-.4 1-.2 1.1.4 2.3.6 3.6.6.6 0 1 .4 1 1V20c0 .6-.4 1-1 1A17 17 0 013 4c0-.6.4-1 1-1h3.5c.6 0 1 .4 1 1 0 1.3.2 2.5.6 3.6.1.3 0 .7-.2 1z"/></svg></div>
    <div>+1 555 010 2040</div>
  </div>
  <div class="contact-row" style="top:246px">
    <div class="ic"><svg width="14" height="11" viewBox="0 0 14 11"><rect width="14" height="11" rx="1.5" fill="#161616"/><path d="M1 1.5l6 4.5 6-4.5" stroke="#fff" stroke-width="1.3" fill="none"/></svg></div>
    <div>info@zvoklinieken.example</div>
  </div>

  <div class="rule"></div>
  <div class="copy">Copyrights@2023.Zvo Klinieken.Alle rechten voorbehouden</div>
</footer>

</body>
</html>
```